Bright bears day nursery qrp limited

we would like create a website that can be updated by us easily as we have regular changes to what we provide and need. we would like something that is classy but also appealing from a child's aspect. we would be looking to add our own logo and our kinderwatch logo both attached, if you guys can create it and we will work with the preferred choice to add all the text.
We would like the links to family pathways, kinderwatch report and our chatterbook feed on the front page

we are looking for a website for our childcare business we have 2 nurseries that we would like one website.
showing our opening hours, price list, policies etc as well as photos, description of our day, staff photos and their training accreditation's.

Target Market(s)

Families

Industry/Entity Type

Childcare

Number of Pages Required

5+ page

Font styles to use
Serif

Colors

Designer to choose colors to be used in the design.

Requirements
Must have
• links to social media and other websites, photographs, links to download registration forms etc, parents able to leave reviews. google maps link, job opportunities
Nice to have
• facilities to take payments

```html
<!DOCTYPE html>
<html lang="en">
<head>
<meta charset="utf-8">
<title>Bright Bears Day Nursery</title>
<link href="https://fonts.googleapis.com/css2?family=Open+Sans:wght@400;600;700;800&display=swap" rel="stylesheet">
<style>
:root{
  --pink:#d6037f;
  --pink-dark:#b0026a;
  --green:#3fae3a;
  --green-light:#52b848;
  --ink:#333;
  --muted:#666;
  --grey-bg:#f2f2f2;
  --footer-bg:#f4f4f4;
  --white:#fff;
  --navy:#2b2f6e;
}
*{box-sizing:border-box;margin:0;padding:0}
html,body{width:1200px;height:4839px;overflow:hidden}
body{font-family:"Open Sans",Arial,sans-serif;color:var(--ink);background:var(--white);position:relative}
.section{position:absolute;left:0;width:1200px}
.section-title{text-align:center;font-weight:700;font-size:28px;color:var(--pink);text-transform:uppercase;letter-spacing:.5px}
.title-rule{width:110px;height:3px;background:var(--pink);margin:14px auto 0;opacity:.7}
.btn{display:inline-block;font-size:15px;font-weight:600;padding:11px 22px;border-radius:2px}
.btn-green{background:var(--green);color:var(--white)}
.btn-outline{border:2px solid #222;color:#222;padding:9px 20px}

/* header */
.site-header{top:0;height:130px;background:var(--white);z-index:3}
.brand{position:absolute;left:96px;top:0;width:190px;height:190px;border-radius:50%;background:var(--white);box-shadow:0 3px 8px rgba(0,0,0,.15);display:flex;flex-direction:column;align-items:center;justify-content:center;text-align:center;z-index:4}
.brand-mark{width:34px;height:34px;background:var(--pink);margin-bottom:10px}
.brand-name{font-weight:800;font-size:22px;line-height:1.1;color:var(--navy);width:140px}
.topbar{position:absolute;top:22px;left:580px;display:flex;align-items:center;gap:12px;font-size:17px;font-weight:600}
.topbar .ico{width:34px;height:34px;border-radius:50%;display:flex;align-items:center;justify-content:center}
.hours{color:var(--pink);margin-right:30px}
.phone{color:var(--green);margin-right:24px}
.socials{display:flex;gap:5px}
.socials span{width:20px;height:20px;border-radius:2px}
.main-nav{position:absolute;top:88px;left:430px;display:flex;gap:60px;font-size:15px;font-weight:600;color:#333}
.main-nav .active{color:var(--pink)}

/* hero */
.hero{top:130px;height:590px}
.hero-photo{position:absolute;inset:0;background:linear-gradient(90deg,#6d7f8a 0%,#9aa8a6 40%,#c9b79a 70%,#a49484 100%)}
.hero-title{position:absolute;left:98px;top:150px;font-size:54px;font-weight:800;color:var(--white);text-shadow:0 2px 0 var(--pink),0 -2px 0 var(--pink),2px 0 0 var(--pink),-2px 0 0 var(--pink)}
.hero-pager{position:absolute;left:100px;top:312px;display:flex;gap:6px}
.hero-pager span{width:13px;height:13px;border-radius:50%;border:2px solid var(--white)}
.hero-pager .on{background:var(--pink);border-color:var(--pink)}
.hero-curve{position:absolute;left:0;bottom:0;width:1200px;height:140px}
.hero-dots{position:absolute;left:560px;bottom:8px;display:flex;gap:6px}
.hero-dots span{width:10px;height:10px;border-radius:50%;background:#c9c9c9}
.hero-dots span:first-child{background:#555}

/* description */
.day{top:780px;text-align:center}
.day p{width:930px;margin:40px auto 0;font-size:13.5px;line-height:1.85;color:var(--muted)}
.day .actions{margin-top:34px;display:flex;justify-content:center;gap:18px}

/* prices */
.prices{top:1123px;height:1017px;background:var(--green-light);color:var(--white);text-align:center}
.prices h2{font-size:30px;font-weight:700;margin-top:60px}
.prices .title-rule{background:var(--white)}
.price-table{position:absolute;left:161px;top:170px;width:878px;border-collapse:collapse;background:var(--white);box-shadow:0 2px 6px rgba(0,0,0,.2)}
.price-table th{background:var(--pink);color:var(--white);height:62px;font-size:18px;font-weight:600}
.price-table td{border:1px solid #e3e3e3;font-size:19px;color:var(--pink);vertical-align:middle}
.price-table td.label{color:var(--green);text-align:left;padding-left:28px;font-size:19px;line-height:1.4;width:200px}
.price-table td .note{display:block;color:var(--green)}
.price-table tr.r1 td{height:140px}
.price-table tr.r2 td{height:147px}
.price-table tr.r3 td{height:177px}
.price-notes{position:absolute;top:740px;width:100%;font-size:19px;font-weight:600;line-height:1.6}
.price-notes p+p{margin-top:24px}
.price-notes .link{margin-top:26px;text-decoration:underline}

/* policies */
.policies{top:2140px;height:466px}
.policies h2{position:absolute;left:100px;top:58px;font-size:28px;color:var(--pink);font-weight:700}
.policies .rule{position:absolute;left:100px;top:106px;width:110px;height:3px;background:var(--pink);opacity:.7}
.policies .copy{position:absolute;left:100px;top:140px;width:570px;font-size:13.5px;line-height:1.85;color:var(--muted)}
.policies .copy p+p{margin-top:14px}
.policies .btn{position:absolute;left:100px;top:352px}
.policies-photo{position:absolute;left:690px;top:70px;width:510px;height:380px;background:radial-gradient(ellipse at 60% 50%,#c9a68d 0%,#e3d5cb 55%,#ffffff 85%)}

/* photos */
.photos{top:2606px;height:734px;background:var(--grey-bg)}
.photos h2{margin-top:54px}
.photo-grid{position:absolute;left:98px;top:162px;width:1000px;display:grid;grid-template-columns:repeat(3,1fr);gap:4px}
.photo-grid div{height:238px}

/* certifications */
.certs{top:3340px;height:340px}
.certs h2{margin-top:66px}
.cert-row{position:absolute;top:183px;left:100px;display:flex;gap:48px}
.cert{width:214px;height:110px;border:1px solid #ddd;display:flex;align-items:center;justify-content:center}
.cert span{width:76px;height:76px;border-radius:50%;background:#bdbdbd}

/* staff */
.staff{top:3680px;height:700px}
.staff-bg{position:absolute;inset:0;width:1200px;height:700px}
.staff h2{position:relative;color:var(--white);margin-top:52px}
.staff .title-rule{background:var(--white)}
.staff-row{position:absolute;top:208px;left:98px;display:flex;gap:33px}
.staff-card{width:225px;height:355px;background:var(--white);text-align:center;padding:8px}
.staff-card .portrait{height:256px;background:linear-gradient(180deg,#d8d8d8,#a9a9a9)}
.staff-card .name{margin-top:22px;font-size:16px;font-weight:700;text-transform:uppercase}
.staff-card .role{font-size:12px;font-weight:700;margin-top:4px;color:#222}
.g{color:var(--green)}
.k{color:#222}

/* footer */
.site-footer{top:4340px;height:499px;background:var(--footer-bg)}
.footer-brands{position:absolute;left:100px;top:150px}
.footer-badge{display:flex;align-items:center;gap:8px;font-size:18px;font-weight:700;color:var(--navy)}
.footer-badge span{width:30px;height:30px;background:var(--navy)}
.footer-badge.alt{margin-top:40px;color:var(--green)}
.footer-badge.alt span{background:var(--green);border-radius:50%}
.footer-col{position:absolute;top:110px}
.footer-col h3{font-size:17px;font-weight:700;color:#333;margin-bottom:24px}
.links{left:305px}
.links li{list-style:none;font-size:14px;color:#555;line-height:2.2}
.links li::before{content:"› ";}
.contact{left:545px}
.contact-item{display:flex;gap:14px;margin-bottom:18px}
.contact-item .ico{width:36px;height:36px;border-radius:50%;border:2px solid var(--pink);flex:none;display:flex;align-items:center;justify-content:center}
.contact-item b{display:block;font-size:15px;color:#333}
.contact-item small{font-size:12.5px;color:#555;line-height:1.5;display:block}
.feed{left:862px}
.feed-item{display:flex;gap:12px;margin-bottom:18px}
.feed-item span{width:34px;height:34px;border-radius:50%;background:#c7cbd6;flex:none}
.feed-item p{font-size:13px;color:#444;line-height:1.45}
.copyright{position:absolute;bottom:0;left:100px;width:1000px;border-top:1px solid #ccc;height:92px;display:flex;align-items:center;justify-content:center;font-size:14.5px;font-weight:700;color:#333}
</style>
</head>
<body>

<header class="section site-header">
  <div class="brand">
    <div class="brand-mark"></div>
    <div class="brand-name">Bright Bears Day Nursery</div>
  </div>
  <div class="topbar">
    <span class="ico" style="background:var(--pink)"><svg width="18" height="18" viewBox="0 0 24 24"><circle cx="12" cy="12" r="9" fill="none" stroke="#fff" stroke-width="2.4"/><path d="M12 7v5l3 2" stroke="#fff" stroke-width="2.4" fill="none"/></svg></span>
    <span class="hours">10 A.M to 6 P.M</span>
    <span class="ico" style="background:var(--green)"><svg width="18" height="18" viewBox="0 0 24 24"><path d="M6 3l4 4-2 3c1 2 3 4 5 5l3-2 4 4-3 3C10 20 4 14 3 6z" fill="#fff"/></svg></span>
    <span class="phone">180 555 0142</span>
    <div class="socials">
      <span style="background:#3aa7e0"></span><span style="background:#1b6fa8"></span><span style="background:#8a8a8a"></span><span style="background:#4466aa"></span><span style="background:#d23a2d"></span>
    </div>
  </div>
  <nav class="main-nav">
    <span class="active">HOME</span><span>ABOUT US</span><span>POLICIES</span><span>CHILD CARE</span><span>BLOG</span><span>CONTACT US</span>
  </nav>
</header>

<section class="section hero">
  <div class="hero-photo" role="img" aria-label="Teacher playing with a young boy and a bead maze toy in a bright classroom"></div>
  <h1 class="hero-title">Bright Bears Day Care<br>Nursery</h1>
  <div class="hero-pager"><span class="on"></span><span></span><span></span><span></span><span></span></div>
  <svg class="hero-curve" viewBox="0 0 1200 140" preserveAspectRatio="none">
    <path d="M0 40 Q600 150 1200 40 L1200 140 L0 140 Z" fill="#fff"/>
    <path d="M0 40 Q600 150 1200 40 L1200 80 Q600 170 0 80 Z" fill="var(--pink)"/>
  </svg>
  <div class="hero-dots"><span></span><span></span><span></span><span></span><span></span></div>
</section>

<section class="section day">
  <h2 class="section-title">Description of our day</h2>
  <div class="title-rule"></div>
  <p>Our day begins with a warm welcome and breakfast, followed by free play, group stories and songs. Children enjoy outdoor time in the garden, creative art sessions and a healthy lunch. Afternoons include quiet rest, sensory play and small group learning, then a light snack before home time with parents and carers.</p>
  <div class="actions"><span class="btn btn-green">Read More</span><span class="btn btn-outline">Contact Us</span></div>
</section>

<section class="section prices">
  <h2>NEW PRICE LIST FROM 1 ST APRIL 2017</h2>
  <table class="price-table">
    <tr><th></th><th>Under 2's</th><th>2-5's</th></tr>
    <tr class="r1"><td class="label">Half day<br>8am-1pm or<br>1pm-6pm</td><td>£26</td><td>£25</td></tr>
    <tr class="r2"><td class="label">Full day<br>(7.30-6pm)</td><td>£168</td><td>£161<span class="note">(Funded children in holidays)</span></td></tr>
    <tr class="r3"><td class="label">Full time<br>funded children<br>3+ years old*</td><td>xxxxxxxxxxx</td><td>£130<span class="note">During term time</span></td></tr>
  </table>
  <div class="price-notes">
    <p>Fees include breakfast (full day/full time only) A light snack each session, nappies<br>and wipes.</p>
    <p>Meals can be offered for an additional charge (£2.50 per meal, per day).<br>Please see a member of staff!</p>
    <p class="link">IS YOU CHILD ENTITLED TO FUNDING?</p>
  </div>
</section>

<section class="section policies">
  <h2>OUR POLICIES</h2>
  <div class="rule"></div>
  <div class="copy">
    <p>We keep every child safe, happy and cared for. Our policies cover safeguarding, health and hygiene, settling in, behaviour, allergies and medicine, and how we share progress with families. Copies of each policy can be read at either nursery or downloaded from this page at any time, and we review them every year.</p>
    <p>Please speak with a nursery manager if you have any questions about our policies or wish to share feedback with us.</p>
  </div>
  <span class="btn btn-green">Read More</span>
  <div class="policies-photo" role="img" aria-label="Teacher and toddler stacking blue wooden blocks at a table"></div>
</section>

<section class="section photos">
  <h2 class="section-title">Our Photos</h2>
  <div class="title-rule"></div>
  <div class="photo-grid">
    <div role="img" aria-label="Children and teacher reading together on the floor" style="background:linear-gradient(135deg,#b58d6c,#d9c0a3)"></div>
    <div role="img" aria-label="Girl playing with colourful building toys" style="background:linear-gradient(135deg,#c9a35a,#e6d08c)"></div>
    <div role="img" aria-label="Group of children drawing at a table" style="background:linear-gradient(135deg,#8fb3c9,#d6c3a5)"></div>
    <div role="img" aria-label="Teacher helping a child with crafts" style="background:linear-gradient(135deg,#c69a6a,#e8cfa7)"></div>
    <div role="img" aria-label="Children playing with an abacus" style="background:linear-gradient(135deg,#9a7a5a,#d7b98e)"></div>
    <div role="img" aria-label="Toddlers building with blocks" style="background:linear-gradient(135deg,#d8b27a,#efe0bf)"></div>
  </div>
</section>

<section class="section certs">
  <h2 class="section-title">Our Certifications</h2>
  <div class="title-rule"></div>
  <div class="cert-row">
    <div class="cert"><span style="background:#d46a6a"></span></div>
    <div class="cert"><span style="background:#8f8466"></span></div>
    <div class="cert"><span style="background:#777"></span></div>
    <div class="cert"><span style="background:#9a2a47;border-radius:6px;width:150px;height:50px"></span></div>
  </div>
</section>

<section class="section staff">
  <svg class="staff-bg" viewBox="0 0 1200 700" preserveAspectRatio="none"><path d="M0 0 H1200 V600 Q600 720 0 600 Z" fill="var(--pink)"/></svg>
  <h2 class="section-title">Our Staff</h2>
  <div class="title-rule"></div>
  <div class="staff-row">
    <div class="staff-card"><div class="portrait" role="img" aria-label="Portrait of teacher Peter Lane"></div><div class="name g">Peter Lane</div><div class="role">TEACHER</div></div>
    <div class="staff-card"><div class="portrait" role="img" aria-label="Portrait of teacher Rachel Moore"></div><div class="name k">Rachel Moore</div><div class="role">TEACHER</div></div>
    <div class="staff-card"><div class="portrait" role="img" aria-label="Portrait of teacher Daniel Hart"></div><div class="name g">Daniel Hart</div><div class="role">TEACHER</div></div>
    <div class="staff-card"><div class="portrait" role="img" aria-label="Portrait of teacher Emma Rose"></div><div class="name k">Emma Rose</div><div class="role">TEACHER</div></div>
  </div>
</section>

<footer class="section site-footer">
  <div class="footer-brands">
    <div class="footer-badge"><span></span>Kinderwatch</div>
    <div class="footer-badge alt"><span></span>Family Pathways</div>
  </div>
  <div class="footer-col links">
    <h3>QUICK LINKS</h3>
    <ul><li>Home</li><li>About Us</li><li>How do You know?</li><li>Who are we?</li><li>More info/Credentials</li><li>Contact Us</li></ul>
  </div>
  <div class="footer-col contact">
    <h3>CONTACT US</h3>
    <div class="contact-item"><span class="ico"><svg width="16" height="16" viewBox="0 0 24 24"><path d="M12 2a7 7 0 0 0-7 7c0 5 7 13 7 13s7-8 7-13a7 7 0 0 0-7-7zm0 9.5A2.5 2.5 0 1 1 12 6.5a2.5 2.5 0 0 1 0 5z" fill="var(--pink)"/></svg></span><div><b>ADDRESS:</b><small>45 Meadow Court,<br>Willow Lane, UK</small></div></div>
    <div class="contact-item"><span class="ico"><svg width="16" height="16" viewBox="0 0 24 24"><path d="M6 3l4 4-2 3c1 2 3 4 5 5l3-2 4 4-3 3C10 20 4 14 3 6z" fill="var(--pink)"/></svg></span><div><b>PHONE:</b><small>180 555 0142</small></div></div>
    <div class="contact-item"><span class="ico"><svg width="16" height="16" viewBox="0 0 24 24"><path d="M3 6h18v12H3z M3 6l9 7 9-7" fill="none" stroke="var(--pink)" stroke-width="2"/></svg></span><div><b>Mail:</b><small>info@brightbearsnursery.example</small></div></div>
  </div>
  <div class="footer-col feed">
    <h3>CHATTERBOOK FEED</h3>
    <div class="feed-item"><span></span><p>Bright Bears Day Nursery QRP<br>July 6 at 3:25pm</p></div>
    <div class="feed-item"><span></span><p>Bright Bears Day Nursery QRP<br>June 6</p></div>
    <div class="feed-item"><span></span><p>familypathways.example<br>June 6</p></div>
  </div>
  <div class="copyright">Copyright © 2017 Bright Bears Day Care Nursery. All Right Reserved</div>
</footer>

</body>
</html>
```